Ridgeway Mining Solutions Business Card

Ridgeway Mining Solutions is a company that provides consulting services to the Mining Industry.

Whilst Ridgeway Mining Solutions is an Australian based company its client base is the global mining industry.

The essence of Ridgeway Mining Solutions is its a can do organisation that can make a difference to its clients by providing quality assistance and form lasting relationships.
Updates

Target Market(s)

The global Mining Industry.

Industry/Entity Type

Mining

Font styles to use
Serif

Colors

Designer to choose colors to be used in the design.

Requirements
Nice to have
• My thinking is the card would look good in black given the logo.

I would like to see written on the back side of the card " Providing Metallurgical, Management and Corporate Services to the Mining Industry"

```html
<!DOCTYPE html>
<html lang="en">
<head>
<meta charset="utf-8">
<title>Ridgeway Mining Solutions — Business Card</title>
<link href="https://fonts.googleapis.com/css2?family=Tinos:wght@400;700&display=swap" rel="stylesheet">
<style>
  :root {
    --stage: #3a3a3a;
    --card-white: #f7f7f7;
    --card-black: #1c1c1c;
    --gold: #f7b127;
    --ink: #222222;
    --paper: #ffffff;
    --muted: #d9d9d9;
  }
  * { margin: 0; padding: 0; box-sizing: border-box; }
  html, body { width: 1200px; height: 960px; overflow: hidden; }
  body {
    background: var(--stage);
    font-family: "Tinos", "Times New Roman", serif;
    position: relative;
  }
  .card {
    position: absolute;
    left: 320px;
    width: 560px;
    height: 320px;
    overflow: hidden;
    box-shadow: 0 10px 30px rgba(0,0,0,.35);
  }
  /* Front */
  .card--front { top: 100px; background: var(--card-white); }
  .edge-stripe { position: absolute; left: 0; top: 0; width: 30px; height: 100%; }
  .edge-stripe__gold { height: 58%; background: var(--gold); }
  .edge-stripe__black { height: 42%; background: var(--ink); }
  .front-rule {
    position: absolute; left: 110px; right: 50px; top: 176px;
    height: 1px; background: var(--gold);
  }
  .front-brand {
    position: absolute; left: 30px; right: 0; top: 96px;
    text-align: center;
  }
  .brand-name {
    color: var(--gold);
    font-weight: 700;
    line-height: 1;
  }
  .front-brand .brand-name { font-size: 44px; background: var(--card-white); display: inline-block; padding: 0 14px; }
  .front-brand .brand-name span { display: block; font-size: 17px; letter-spacing: 4px; margin-top: 6px; }
  .tagline {
    position: absolute; left: 30px; right: 0; top: 206px;
    text-align: center; font-size: 15px; color: var(--ink);
  }
  /* Back */
  .card--back { top: 540px; background: var(--card-black); color: var(--paper); }
  .back-graphics { position: absolute; inset: 0; }
  .back-brand { position: absolute; left: 42px; top: 92px; }
  .back-brand .brand-name { font-size: 34px; }
  .back-brand .brand-name span { display: block; font-size: 13px; letter-spacing: 3px; margin-top: 4px; }
  .person-name {
    position: absolute; left: 42px; top: 206px;
    font-size: 19px; color: var(--ink);
  }
  .person-role {
    position: absolute; left: 330px; top: 160px;
    font-size: 12px; color: var(--paper);
  }
  .address {
    position: absolute; left: 42px; top: 262px;
    font-size: 13px; line-height: 1.3; color: var(--paper);
  }
  .contacts {
    position: absolute; left: 350px; top: 212px;
    list-style: none; font-size: 13px;
  }
  .contacts li { display: flex; align-items: center; gap: 10px; height: 24px; }
  .contacts svg { width: 14px; height: 14px; flex: none; }
</style>
</head>
<body>

<section class="card card--front" aria-label="Card front">
  <div class="edge-stripe">
    <div class="edge-stripe__gold"></div>
    <div class="edge-stripe__black"></div>
  </div>
  <div class="front-rule"></div>
  <div class="front-brand">
    <p class="brand-name">Ridgeway<span>MINING SOLUTIONS</span></p>
  </div>
  <p class="tagline">We provide consulting services to the Mining Industry.</p>
</section>

<section class="card card--back" aria-label="Card back">
  <svg class="back-graphics" viewBox="0 0 560 320" aria-hidden="true">
    <polygon points="0,196 262,196 236,236 0,236" fill="#ffffff"/>
    <polygon points="270,196 282,196 262,214 250,214" fill="#ffffff"/>
    <polygon points="290,190 302,190 282,208 270,208" fill="#ffffff"/>
    <polygon points="310,184 322,184 302,202 290,202" fill="#ffffff"/>
    <line x1="322" y1="182" x2="560" y2="182" stroke="#ffffff" stroke-width="3"/>
  </svg>

  <div class="back-brand">
    <p class="brand-name">Ridgeway<span>MINING SOLUTIONS</span></p>
  </div>
  <p class="person-role">Managing Director</p>
  <p class="person-name">Daniel Marsh</p>
  <p class="address">Harbour Consulting Pty 000<br>Ave Kalgoorlie, WA 0000</p>

  <ul class="contacts">
    <li>
      <svg viewBox="0 0 16 16" aria-hidden="true"><path fill="#f7b127" d="M3 2h3l1 3-2 1c1 2 2 3 4 4l1-2 3 1v3c0 1-1 2-2 2C6 14 2 10 2 4c0-1 0-2 1-2z"/></svg>
      <span>0044 5678 123</span>
    </li>
    <li>
      <svg viewBox="0 0 16 16" aria-hidden="true"><rect x="1" y="3" width="14" height="10" fill="#f7b127"/><path d="M1 3l7 6 7-6" stroke="#1c1c1c" stroke-width="1.3" fill="none"/></svg>
      <span>info@ridgewaymining.com</span>
    </li>
    <li>
      <svg viewBox="0 0 16 16" aria-hidden="true"><rect x="1.5" y="2.5" width="13" height="9" fill="none" stroke="#f7b127" stroke-width="1.5"/><path d="M5 14h6M8 11.5V14" stroke="#f7b127" stroke-width="1.5"/></svg>
      <span>www.ridgewaymining.com</span>
    </li>
  </ul>
</section>

</body>
</html>
```